Redesign of business card for Cedar Ridge Mechanical

We are looking for a new design for our business cards for Cedar Ridge Mechanical. We are a plumbing & HVAC construction company, operating on the West Coast of Canada and USA. Logo attached.
Industry/Entity Type
Construction - Plumbing & HVAC
Contact Information for Business Card
Name, address, phone numbers, email, website address
Look and feel
Each slider illustrates characteristics of the customer's brand and the style your logo design should communicate.

```html
<!DOCTYPE html>
<html lang="en">
<head>
<meta charset="utf-8">
<title>Cedar Ridge Mechanical – Business Card</title>
<link rel="stylesheet" href="https://fonts.googleapis.com/css2?family=Montserrat:wght@400;500;600;700&display=swap">
<style>
  :root {
    --backdrop: #1c1c1e;
    --card-black: #121212;
    --card-black-soft: #1f1f1f;
    --card-white: #ffffff;
    --stripe-grey: #9a9a9a;
    --ink-dark: #1a1a1a;
    --ink-grey: #8c8c8c;
    --ink-mid: #5a5a5a;
    --logo-grey: #4a4a4a;
  }
  * { box-sizing: border-box; margin: 0; padding: 0; }
  html, body {
    width: 1200px; height: 801px; overflow: hidden;
    background: var(--backdrop);
    font-family: "Montserrat", sans-serif;
  }
  .canvas {
    position: relative; width: 1200px; height: 801px;
    display: flex; align-items: center; justify-content: center; gap: 60px;
  }
  .card {
    position: relative; width: 520px; height: 300px;
    border-radius: 22px; overflow: hidden;
    box-shadow: 0 18px 40px rgba(0,0,0,.55);
  }

  /* Front */
  .card-front { background: var(--card-white); }
  .front-band {
    position: absolute; left: 0; top: 0; width: 100%; height: 124px;
    background: linear-gradient(160deg, var(--card-black-soft), var(--card-black) 60%);
  }
  .front-stripe {
    position: absolute; left: 0; top: 130px; width: 100%; height: 7px;
    background: var(--stripe-grey);
  }
  .brand-name {
    position: absolute; left: 0; top: 50px; width: 100%;
    text-align: center; white-space: nowrap;
    color: var(--card-white); font-weight: 600; font-size: 16px;
    letter-spacing: 2px; text-transform: uppercase;
  }
  .holder {
    position: absolute; left: 20px; top: 172px; width: 200px;
    text-align: right; white-space: nowrap;
  }
  .holder-name { font-weight: 700; font-size: 16px; letter-spacing: 1px; color: var(--ink-dark); }
  .holder-name .surname { color: var(--ink-grey); }
  .holder-role { font-weight: 500; font-size: 13px; color: var(--ink-dark); margin-top: 3px; }
  .divider {
    position: absolute; left: 236px; top: 162px; width: 1px; height: 64px;
    background: var(--ink-grey);
  }
  .contacts { position: absolute; left: 252px; top: 160px; list-style: none; }
  .contacts li {
    display: flex; align-items: center; gap: 7px; white-space: nowrap;
    font-size: 14px; color: var(--ink-grey); line-height: 22px;
  }
  .contacts li strong { font-weight: 500; color: var(--ink-mid); }
  .contacts svg { width: 12px; height: 12px; fill: var(--ink-mid); flex: none; }
  .address {
    position: absolute; left: 0; top: 250px; width: 100%;
    text-align: center; white-space: nowrap;
    font-size: 14px; color: var(--ink-grey); letter-spacing: .3px;
  }

  /* Back */
  .card-back {
    background: linear-gradient(135deg, #2a2a2a 0%, var(--card-black) 45%, #0c0c0c 100%);
    display: flex; align-items: center; justify-content: center;
  }
  .back-name {
    color: var(--logo-grey); font-weight: 600; font-size: 28px;
    letter-spacing: 2px; text-transform: uppercase; line-height: 1.25;
    text-align: center;
  }
</style>
</head>
<body>
<main class="canvas">
  <section class="card card-front" aria-label="Business card front">
    <div class="front-band"></div>
    <div class="front-stripe"></div>
    <p class="brand-name">Cedar Ridge Mechanical</p>
    <div class="holder">
      <p class="holder-name">JONATHAN <span class="surname">SMITH</span></p>
      <p class="holder-role">Manager</p>
    </div>
    <div class="divider"></div>
    <ul class="contacts">
      <li>
        <svg viewBox="0 0 24 24"><path d="M6.6 10.8a15 15 0 0 0 6.6 6.6l2.2-2.2c.3-.3.7-.4 1-.2 1.1.4 2.3.6 3.6.6.6 0 1 .4 1 1V20c0 .6-.4 1-1 1A17 17 0 0 1 3 4c0-.6.4-1 1-1h3.5c.6 0 1 .4 1 1 0 1.3.2 2.5.6 3.6.1.3 0 .7-.2 1z"/></svg>
        123-456-2100
      </li>
      <li>
        <svg viewBox="0 0 24 24"><path d="M2 5h20v14H2zm2 2v.5l8 5 8-5V7l-8 5z"/></svg>
        youremail@cedarmail.com
      </li>
      <li>
        <svg viewBox="0 0 24 24"><circle cx="12" cy="12" r="10"/></svg>
        <span>www.<strong>yourwebsite</strong>.com</span>
      </li>
    </ul>
    <p class="address">Your address, city, state, ZIP 0000</p>
  </section>

  <section class="card card-back" aria-label="Business card back">
    <p class="back-name">Cedar Ridge<br>Mechanical</p>
  </section>
</main>
</body>
</html>
```